Golf Brochure + Business Card Design Project – Kestrel Fitness.

Task Description

We are looking for a premium tri-fold brochure (8.5x11 letter, folded) plus a new business card design for Kestrel Fitness. Both need to look polished, elegant, and professional — something that would feel at home in a golf club environment.

Brochure Scope:
• Tri-fold brochure promoting our new golf-specific services
• Incorporate brand colors: deep hunter green, cream, and gold accents
• Clean, modern typography (professional, not playful)
• Layout will follow the copy provided (final copy attached, no rewriting needed)
• Imagery: mature golfers (50+), golf lifestyle shots, no generic stocky images
• Include QR code placement linking to booking page
• Deliverables: print-ready PDF with bleed/crop (CMYK), high-res PDF (digital), and source file (InDesign or Illustrator)

Business Card Scope:
• Front + back design
• Consistent with brand colors and fonts
• Space for name, title, phone, email, and website
• Deliverables: print-ready PDF with bleed/crop (CMYK) + source file (AI or InDesign)
• If possible, provide editable template for future staff cards

Timeline:
• First draft within 5–7 days
• 2 rounds of revisions included

Budget:
$300 USD (total for both brochure + business card)

I’ll provide finalized copy if you accept the project.
Project description (paste this whole block in that box)

We need a premium tri-fold brochure (8.5”×11” letter, folded) and a new business card design for Kestrel Fitness. This will be presented to golf course managers and members, so the look must be elegant, restrained, and country-club-classy.

Scope — Brochure
• Format: Tri-fold, 8.5”×11”. Please set 0.125” bleed on all sides and keep critical text ≥0.125–0.25” inside the trim.
• Purpose: Promote Kestrel Fitness’ golf-specific services for adults 50+.
• Copy: We will provide finalized copy in a Word doc after acceptance. No rewriting needed — please focus on layout and polish.
• Imagery (required):
• Golf-first images (ball on tee/green, mature golfers mid-swing, and golf course landscapes at golden hour).
• 1–2 real Kestrel Fitness gym photos on inside panels (trainer with client doing golf-relevant movement: stretch, rotation, balance).
• Visual style: Premium, quiet, lots of white/negative space, balanced grids; no clutter.
• Brand colors (required): Hunter Green #0C2E1F, Gold #CBA135, Cream #F5F2EB. Convert for CMYK print while preserving the look.
• Typography: Clean, legible serif + sans pairing (e.g., modern serif for headlines, humanist/neo-grotesk sans for body). You may propose suitable professional fonts; avoid playful/novelty fonts.
• Elements to include:
• Our logo (we will upload).
• QR code placement to booking page (we will supply the URL / QR asset).
• Simple icon treatment for the three complimentary options (Strength & Mobility, Stretch Therapy, Vitrascan + Assessment).
• Deliverables:
• Print-ready PDF (CMYK, with bleed & crop marks, PDF/X-1a or PDF/X-4)
• High-res digital PDF (no bleed)
• Source file (InDesign or Illustrator) + packaged fonts/links or outlined type as appropriate.

Scope — Business Card
• Size: 3.5”×2” (US standard) with 0.125” bleed; keep text ≥0.125” from trim.
• Front/back design; consistent with brochure branding.
• Fields: Name, Title, Phone, Email, Website, Address; optional small QR on back.
• Deliverables: Print-ready PDF (CMYK, bleed & crops) + Source file (AI/INDD). Provide an editable template for staff names.

Process & Timing
• Initial concept for brochure + card within 5–7 days of acceptance.
• 2 rounds of revisions included.
• Please start with a clean layout concept using placeholder images/text blocks; we’ll drop in final copy/assets immediately after acceptance.

Stock & Licensing
• You may propose stock images that fit the brief (we’re fine approving Pixelgrove or equivalent). Please note any license fees separately if needed.

Usage Rights
• We require full usage rights to the final designs for print & digital.

Target Market(s)

Golfers 50+ in Victoria, BC: quality-oriented, health-conscious, want to play longer, stronger, and pain-free. Country-club aesthetic; expect polished, professional materials.

Industry/Entity Type

Health & Fitness — Golf Performance / Longevity Studio

Font styles to use
Serif
Sans Serif

Requirements
Must have
• • Golf-first imagery + 1–2 real Kestrel Fitness photos inside. • Brand colors: #0C2E1F (Hunter Green), #CBA135 (Gold), #F5F2EB (Cream). • Premium, restrained layout; ample negative space; no clutter. • Clean professional serif + sans type pairing; highly legible. • Space for logo and QR code (booking). • Correct print specs (bleed, crops, CMYK). • Deliverables: print-ready PDFs (brochure + card), digital PDF, source files.
Nice to have
• • Subtle texture or grain in backgrounds (very light) to add sophistication. • A second brochure cover variation (ball on tee vs. course landscape) at concept stage.
Should not have
• • Cheesy/posed “stocky” groups; overly young models; beer/alcohol imagery. • Over-saturated greens/blues; gimmicky gradients or clip art. • Generic fitness/bodybuilding shots unrelated to golf performance.

```html
<!DOCTYPE html>
<html lang="en">
<head>
<meta charset="utf-8">
<title>Kestrel Fitness – Business Card</title>
<link href="https://fonts.googleapis.com/css2?family=Josefin+Sans:wght@600&family=Roboto:wght@400;700&display=swap" rel="stylesheet">
<style>
  :root {
    --stage: #8a8d8e;
    --hunter: #12302e;
    --hunter-deep: #0f2a28;
    --hunter-light: #2b4744;
    --gold: #b59a4c;
    --gold-text: #8a6d10;
    --cream: #f7f4ec;
    --ink: #2a2a2a;
    --silhouette: #2b2726;
  }
  * { margin: 0; padding: 0; box-sizing: border-box; }
  html, body { width: 1077px; height: 1200px; overflow: hidden; }
  body { background: var(--stage); position: relative; }

  .card { position: absolute; left: 108px; width: 861px; height: 492px; overflow: hidden; }
  .card-front { top: 88px; background: var(--hunter-deep); }
  .card-back { top: 620px; background: var(--cream); }

  .frame { position: absolute; inset: 12px; border: 1px solid var(--gold); }
  .frame::after { content: ""; position: absolute; inset: 4px; border: 1px solid var(--gold); }

  .front-photo {
    position: absolute; inset: 0;
    background: radial-gradient(ellipse 45% 75% at 50% 55%, var(--hunter-light) 0%, #1f3b38 55%, var(--hunter-deep) 100%);
  }

  .brand { position: absolute; left: 0; right: 0; top: 70px; text-align: center; }
  .brand-circle { width: 128px; height: 128px; border: 4px solid var(--gold); border-radius: 50%; margin: 0 auto; }
  .brand-name {
    margin-top: 22px; font-family: "Josefin Sans", sans-serif; font-weight: 600;
    font-size: 32px; letter-spacing: 6px; color: var(--gold);
  }

  .tagline {
    position: absolute; left: 0; right: 0; top: 360px; text-align: center;
    font-family: "Josefin Sans", sans-serif; font-weight: 600; font-size: 39px;
    letter-spacing: 1px; color: #ffffff; white-space: nowrap;
  }
  .tagline .accent { color: var(--gold); }

  .golfer {
    position: absolute; left: 38px; top: 39px; width: 370px; height: 416px;
    background: radial-gradient(ellipse 30% 48% at 38% 55%, var(--silhouette) 0%, rgba(43,39,38,0.55) 55%, rgba(43,39,38,0) 100%);
  }

  .details { position: absolute; left: 400px; top: 104px; font-family: "Roboto", sans-serif; }
  .person-name { font-weight: 700; font-size: 42px; color: var(--hunter); letter-spacing: -0.3px; line-height: 1; }
  .person-title { margin-top: 12px; font-size: 30px; color: var(--gold-text); line-height: 1; }

  .contact-list { list-style: none; margin-top: 36px; }
  .contact-item { display: flex; align-items: center; height: 31px; margin-bottom: 25px; font-size: 17px; color: var(--ink); }
  .contact-icon { width: 31px; height: 31px; border-radius: 50%; display: flex; align-items: center; justify-content: center; margin-right: 20px; }
  .contact-icon.gold { background: var(--gold); }
  .contact-icon.green { background: var(--hunter); }
</style>
</head>
<body>
  <section class="card card-front">
    <div class="front-photo" role="img" aria-label="Close-up of a golf ball resting in grass, darkened in hunter green"></div>
    <div class="frame"></div>
    <div class="brand">
      <div class="brand-circle"></div>
      <div class="brand-name">KESTREL FITNESS</div>
    </div>
    <p class="tagline">STRENGTH • <span class="accent">MOBILITY</span> • LONGEVITY</p>
  </section>

  <section class="card card-back">
    <div class="frame"></div>
    <div class="golfer" role="img" aria-label="Dark silhouette of a golfer finishing a full swing"></div>
    <div class="details">
      <h1 class="person-name">Margot-Jane Whitlow</h1>
      <p class="person-title">Owner | Kestrel Fitness</p>
      <ul class="contact-list">
        <li class="contact-item">
          <span class="contact-icon gold">
            <svg width="14" height="14" viewBox="0 0 24 24"><path fill="#fff" d="M6.6 10.8a15.1 15.1 0 0 0 6.6 6.6l2.2-2.2a1 1 0 0 1 1-.25 11.4 11.4 0 0 0 3.6.57 1 1 0 0 1 1 1V20a1 1 0 0 1-1 1A17 17 0 0 1 3 4a1 1 0 0 1 1-1h3.5a1 1 0 0 1 1 1c0 1.25.2 2.45.57 3.57a1 1 0 0 1-.25 1z"/></svg>
          </span>250-555-0147
        </li>
        <li class="contact-item">
          <span class="contact-icon green">
            <svg width="14" height="12" viewBox="0 0 24 20"><rect x="1" y="2" width="22" height="16" rx="2" fill="#fff"/><path d="M2 4l10 7 10-7" fill="none" stroke="#12302e" stroke-width="2"/></svg>
          </span>margot-jane@kestrelfitness.biz
        </li>
        <li class="contact-item">
          <span class="contact-icon gold">
            <svg width="14" height="14" viewBox="0 0 24 24"><circle cx="12" cy="12" r="10" fill="#fff"/><path d="M2 12h20M12 2c3 3 3 17 0 20M12 2c-3 3-3 17 0 20" fill="none" stroke="#b59a4c" stroke-width="1.6"/></svg>
          </span>kestrelfitnessvictoria.com
        </li>
      </ul>
    </div>
  </section>
</body>
</html>
```